Business card design Needed for new logo / Construction business, home extensions and new builds

We need a business card design using our new logo files which i will attach to this project :)

We are a small construction business specialising in home extensions, new builds and property development. We are very ambitious and would appreciate professional and elegant designs for our new business card.

Very serious about using the services on MakerQuarry and recently acquired our new logo from here :)

Please get involved, i will feedback when i can as i am very busy but can respond daily, thanks

Target Market(s)

People that want to build onto their houses, new building developments or adding too their existing property

Industry/Entity Type

Construction

Contact Information for Business Card

Renwick Tolliver Construction, Lionel Ashby (Managing Director), Tel 07822254961, email - info@renwick-tolliver, www.renwick-tolliver.co.uk

Colors

Designer to choose colors to be used in the design.

Requirements
Must have
• I like a deep grey on the back please. A lot of you have provided black from and back, try mixing things up a little. The black looks cool 😎 Thanks

```html
<!DOCTYPE html>
<html lang="en">
<head>
<meta charset="utf-8">
<title>Renwick Tolliver Construction – Business Card</title>
<link href="https://fonts.googleapis.com/css2?family=Cinzel:wght@500;600&family=Lato:wght@400;700&display=swap" rel="stylesheet">
<style>
  :root {
    --stage: #2a2a2a;
    --card-black: #1b1b1c;
    --gold-light: #f7d58a;
    --gold-mid: #e0a93a;
    --gold-deep: #bf8117;
    --silver: #d9dadc;
    --ink: #141414;
  }
  * { box-sizing: border-box; margin: 0; padding: 0; }
  html, body { width: 1200px; height: 875px; overflow: hidden; }
  body {
    background: var(--stage);
    display: flex;
    align-items: center;
    justify-content: center;
    gap: 40px;
    font-family: "Lato", sans-serif;
  }
  .card {
    position: relative;
    width: 540px;
    height: 310px;
    border-radius: 16px;
    overflow: hidden;
    box-shadow: 0 18px 40px rgba(0,0,0,0.45);
  }

  /* Front */
  .card-front {
    background: var(--card-black);
    display: flex;
    align-items: center;
    justify-content: center;
  }
  .brand {
    display: flex;
    align-items: center;
    gap: 14px;
    font-family: "Cinzel", serif;
    font-weight: 600;
    color: var(--gold-mid);
    font-size: 25px;
    letter-spacing: 0.06em;
    text-transform: uppercase;
  }
  .brand-square {
    width: 14px;
    height: 14px;
    background: var(--gold-mid);
  }

  /* Back */
  .card-back {
    background: linear-gradient(115deg, var(--gold-light) 0%, var(--gold-mid) 45%, var(--gold-deep) 70%, var(--gold-mid) 100%);
  }
  .corner-panel {
    position: absolute;
    inset: 0;
    width: 540px;
    height: 310px;
  }
  .corner-brand {
    position: absolute;
    top: 92px;
    left: 348px;
    width: 180px;
    display: flex;
    align-items: center;
    gap: 8px;
    font-family: "Cinzel", serif;
    font-weight: 600;
    font-size: 15px;
    letter-spacing: 0.05em;
    color: var(--gold-mid);
    text-transform: uppercase;
    line-height: 1.2;
  }
  .corner-brand .brand-square { width: 10px; height: 10px; flex: none; }
  .contact {
    position: absolute;
    left: 34px;
    top: 96px;
    color: var(--ink);
  }
  .contact-name {
    font-family: "Cinzel", serif;
    font-weight: 500;
    font-size: 23px;
    letter-spacing: 0.03em;
    text-transform: uppercase;
  }
  .contact-role {
    font-weight: 700;
    font-size: 14px;
    margin-top: 2px;
  }
  .contact-address {
    margin-top: 14px;
    font-size: 13px;
    line-height: 1.35;
  }
  .contact-address strong { font-weight: 700; }
  .contact-lines {
    list-style: none;
    margin-top: 12px;
    font-size: 13px;
    line-height: 1.5;
  }
  .contact-lines li { display: flex; align-items: center; gap: 8px; }
  .contact-lines svg { width: 12px; height: 12px; fill: var(--ink); flex: none; }
</style>
</head>
<body>

  <section class="card card-front">
    <div class="brand">
      <span class="brand-square"></span>
      <span>Renwick Tolliver Construction</span>
    </div>
  </section>

  <section class="card card-back">
    <svg class="corner-panel" viewBox="0 0 540 310" aria-hidden="true">
      <polygon points="290,0 318,214 540,262 540,0" fill="#1b1b1c"/>
      <polyline points="280,0 309,222 540,272" fill="none" stroke="#d9dadc" stroke-width="4"/>
    </svg>
    <div class="corner-brand">
      <span class="brand-square"></span>
      <span>Renwick Tolliver</span>
    </div>

    <div class="contact">
      <h1 class="contact-name">Lionel Ashby</h1>
      <p class="contact-role">Managing Director</p>
      <p class="contact-address">
        <strong>Renwick Tolliver Construction</strong><br>
        Your Address, City<br>
        State, Zip 1235
      </p>
      <ul class="contact-lines">
        <li>
          <svg viewBox="0 0 24 24"><path d="M6.6 10.8a15.1 15.1 0 0 0 6.6 6.6l2.2-2.2a1 1 0 0 1 1-.25 11.4 11.4 0 0 0 3.6.57 1 1 0 0 1 1 1V20a1 1 0 0 1-1 1A17 17 0 0 1 3 4a1 1 0 0 1 1-1h3.5a1 1 0 0 1 1 1c0 1.25.2 2.45.57 3.57a1 1 0 0 1-.25 1z"/></svg>
          07822254961
        </li>
        <li>
          <svg viewBox="0 0 24 24"><path d="M2 5h20v14H2z M2 5l10 8 10-8" stroke="#141414" stroke-width="0" /><path d="M2 6.5V19h20V6.5l-10 7.5z M3 5l9 6.8L21 5z"/></svg>
          info@renwick-tolliver.co.uk
        </li>
        <li>
          <svg viewBox="0 0 24 24"><path d="M12 2a10 10 0 1 0 0 20 10 10 0 0 0 0-20zm6.9 6h-3a15.6 15.6 0 0 0-1.3-3.9A8 8 0 0 1 18.9 8zM12 4c.8 1.2 1.5 2.5 1.9 4h-3.8c.4-1.5 1.1-2.8 1.9-4zM4.3 14a8 8 0 0 1 0-4h3.3a16 16 0 0 0 0 4zm.8 2h3a15.6 15.6 0 0 0 1.3 3.9A8 8 0 0 1 5.1 16zm3-8h-3a8 8 0 0 1 4.3-3.9A15.6 15.6 0 0 0 8.1 8zM12 20c-.8-1.2-1.5-2.5-1.9-4h3.8c-.4 1.5-1.1 2.8-1.9 4zm2.3-6H9.7a14.5 14.5 0 0 1 0-4h4.6a14.5 14.5 0 0 1 0 4zm.3 5.9a15.6 15.6 0 0 0 1.3-3.9h3a8 8 0 0 1-4.3 3.9zm1.8-5.9a16 16 0 0 0 0-4h3.3a8 8 0 0 1 0 4z"/></svg>
          renwick-tolliver.co.uk
        </li>
      </ul>
    </div>
  </section>

</body>
</html>
```